Design a Travel and Tourism website

We would like a freelancer to design a website that is essentially easy to use and navigate database providing local information for Travelers about destination countries.

We proposed website would discuss different rates, fees, visa requirement, resort locations, cheap flights, etc. This website should be elegant and modern. Our business name is rovanix.
Some reference websites are zemplorift.ca, brindlefoxhaven.com,
There should be a forum in the website where travell\ers discuss about their first hand tranvel experience to such destinations.

Tourism

```html
<!DOCTYPE html>
<html lang="en">
<head>
<meta charset="utf-8">
<title>Rovanix – Travel Deals</title>
<link href="https://fonts.googleapis.com/css2?family=Open+Sans:wght@300;400;600;700&family=Ubuntu:wght@400;500;700&display=swap" rel="stylesheet">
<style>
:root{
  --blue:#2a8cf0;
  --blue-title:#1f7fe0;
  --ink:#333;
  --muted:#777;
  --soft:#f2f2f2;
  --white:#fff;
  --panel:rgba(30,40,45,.55);
  --line:#ccc;
}
*{box-sizing:border-box;margin:0;padding:0}
html,body{width:728px;height:1200px;overflow:hidden}
body{position:relative;font-family:"Open Sans",sans-serif;color:var(--ink);background:var(--white)}
.abs{position:absolute}
/* header */
.site-header{position:absolute;left:0;top:0;width:728px;height:70px;background:var(--white)}
.brand{left:81px;top:16px;font-size:25px;font-weight:300;color:var(--blue);letter-spacing:.3px}
.util-nav{right:80px;top:14px;font-size:7.2px;color:#444}
.util-nav span{margin:0 2px}
.main-nav{top:45px;font-size:7.2px;color:#444}
.main-nav a{position:absolute;white-space:nowrap;color:#444;text-decoration:none}
.main-nav a.active{color:var(--blue)}
/* hero */
.hero{left:0;top:70px;width:728px;height:303px;
  background:linear-gradient(180deg,#3f8b8a 0%,#6f9f7c 30%,#8c8a55 55%,#9aa03a 80%,#6e8a2a 100%)}
.hero-tent{right:0;top:60px;width:150px;height:243px;background:linear-gradient(135deg,#f2a81e,#d8542a 60%,#b63a2a)}
.search-panel{left:80px;top:94px;width:568px;height:248px;background:var(--panel);border-radius:2px}
.tab{position:absolute;top:12px;width:53px;height:44px;background:rgba(255,255,255,.18);color:#fff;font-size:8.5px;text-align:center;padding-top:28px}
.tab.active{background:var(--blue)}
.tab svg{position:absolute;left:18px;top:8px}
.radios{top:76px;left:20px;font-size:7.2px;color:#fff}
.radios span{margin-right:10px}
.radios i{display:inline-block;width:4px;height:4px;border-radius:50%;background:#fff;margin-right:7px;vertical-align:1px}
.lbl{position:absolute;font-size:7.2px;color:#fff}
.field{position:absolute;height:17px;background:#fff;font-size:6.5px;color:#444;padding:5px 6px;line-height:7px}
.field .pin{color:var(--blue);margin-right:4px}
.field .cal{position:absolute;right:5px;top:4px;width:8px;height:8px;border:1px solid var(--blue)}
.field .chev{position:absolute;right:8px;top:5px;width:4px;height:4px;border-right:1px solid #444;border-bottom:1px solid #444;transform:rotate(45deg)}
.checks{top:192px;left:21px;font-size:7.2px;color:#fff}
.checks span{margin-right:8px}
.checks i{display:inline-block;width:7px;height:7px;background:#fff;margin-right:6px;vertical-align:-1px;border:1.5px solid var(--blue)}
.btn-search{left:11px;top:211px;width:82px;height:22px;background:var(--blue);color:#fff;font-family:"Ubuntu",sans-serif;font-size:11px;font-weight:500;text-align:center;line-height:22px;border-radius:2px}
/* deals */
.deals{left:0;top:373px;width:728px;height:365px;background:var(--soft)}
.section-title{font-family:"Ubuntu",sans-serif;font-weight:700;color:var(--blue-title)}
.deals h2{position:absolute;top:36px;width:728px;text-align:center;font-size:19px}
.deal-card{position:absolute;top:79px;width:182px;height:210px;background:var(--white);border:1px solid #ddd}
.deal-card .photo{height:112px}
.deal-card h3{position:absolute;left:12px;top:131px;font-family:"Ubuntu",sans-serif;font-size:8.6px;font-weight:500;color:var(--blue-title)}
.deal-card p{position:absolute;left:12px;top:149px;width:160px;font-size:6.3px;line-height:14.5px;color:#444}
.deal-card.faded p{color:#999}
.dots{top:318px;left:349px}
.dots i{display:inline-block;width:4px;height:4px;border-radius:50%;background:#bbb;margin-right:9px}
.dots i.on{background:var(--blue)}
/* promos */
.promo{position:absolute;top:769px;width:182px;height:124px}
.btn-explore{position:absolute;top:84px;height:19px;padding:0 8px;background:var(--blue);color:#fff;font-size:7px;line-height:19px;border-radius:1px}
/* footer */
.site-footer{left:0;top:926px;width:728px;height:274px;background:var(--soft)}
.site-footer h2{position:absolute;top:27px;font-family:"Ubuntu",sans-serif;font-size:13px;font-weight:400;color:var(--blue-title)}
.link-col{position:absolute;top:59px;font-size:6.4px;color:#777;line-height:14.5px;list-style:none}
.site-footer h3{position:absolute;left:80px;top:172px;font-family:"Ubuntu",sans-serif;font-size:12px;font-weight:400;color:#222}
.site-footer .about{position:absolute;left:80px;top:198px;width:570px;font-size:6.3px;line-height:14.5px;color:#777}
.rule{position:absolute;left:80px;top:240px;width:568px;height:1px;background:var(--line)}
.copy{position:absolute;left:80px;top:250px;font-size:6.5px;color:#333}
.social{position:absolute;top:249px;width:9px;height:9px;border-radius:50%;background:#222}
</style>
</head>
<body>

<header class="site-header">
  <div class="abs brand">Rovanix</div>
  <nav class="abs util-nav">Account <span>|</span> My Scratchpad <span>|</span> My Trips <span>|</span> Support <span>|</span> Français</nav>
  <nav class="abs main-nav" style="left:0;width:728px">
    <a class="active" style="left:244px">Flights</a>
    <a style="left:288px">Train</a>
    <a style="left:327px">Hotels</a>
    <a style="left:370px">Cars</a>
    <a style="left:407px">Insurance</a>
    <a style="left:461px">Reload Vouchers</a>
    <a style="left:537px">Money Transfer</a>
    <a style="left:609px">Bill Payment</a>
  </nav>
</header>

<section class="abs hero" role="img" aria-label="Photo of a traveller relaxing in a camp chair beside an orange tent on a grassy mountain meadow">
  <div class="abs hero-tent"></div>
</section>

<form class="abs search-panel" aria-label="Flight search">
  <div class="tab active" style="left:11px">
    <svg width="16" height="14" viewBox="0 0 16 14"><path d="M1 8 L15 2 L13 5 L8 7 L9 12 L7 12 L5 8 L2 9 Z" fill="#fff"/></svg>Flights</div>
  <div class="tab" style="left:66px">
    <svg width="16" height="16" viewBox="0 0 16 16"><rect x="3" y="1" width="10" height="11" rx="2" fill="none" stroke="#fff" stroke-width="1.6"/><line x1="3" y1="6" x2="13" y2="6" stroke="#fff" stroke-width="1.4"/><line x1="5" y1="12" x2="3" y2="15" stroke="#fff" stroke-width="1.4"/><line x1="11" y1="12" x2="13" y2="15" stroke="#fff" stroke-width="1.4"/></svg>Train</div>
  <div class="tab" style="left:121px">
    <svg width="18" height="14" viewBox="0 0 18 14"><rect x="1" y="2" width="2" height="11" fill="#fff"/><rect x="1" y="8" width="16" height="3" fill="#fff"/><rect x="7" y="4" width="10" height="4" fill="#fff"/><circle cx="5" cy="6" r="2" fill="#fff"/><rect x="15" y="8" width="2" height="5" fill="#fff"/></svg>Hotels</div>
  <div class="tab" style="left:176px">
    <svg width="18" height="14" viewBox="0 0 18 14"><path d="M3 6 L5 1 H13 L15 6 H17 V11 H1 V6 Z" fill="#fff"/><circle cx="5" cy="12" r="1.6" fill="#fff"/><circle cx="13" cy="12" r="1.6" fill="#fff"/></svg>Cars</div>
  <div class="tab" style="left:231px">
    <svg width="16" height="16" viewBox="0 0 16 16"><circle cx="8" cy="5" r="3.5" fill="#fff"/><path d="M1 16 C1 10 15 10 15 16 Z" fill="#fff"/></svg>Insurance</div>

  <div class="abs radios"><span><i></i>Roundtrip</span><span><i></i>Oneway</span><span><i></i>Multiple destination</span></div>

  <span class="lbl" style="left:12px;top:99px">Flying From</span>
  <span class="lbl" style="left:168px;top:99px">Flying to</span>
  <div class="field" style="left:12px;top:108px;width:148px"><span class="pin">⚲</span>City, or Airport</div>
  <div class="field" style="left:166px;top:108px;width:149px"><span class="pin">⚲</span>Cit of Airport</div>

  <span class="lbl" style="left:12px;top:142px">Departured</span>
  <span class="lbl" style="left:87px;top:142px">Arriving</span>
  <span class="lbl" style="left:165px;top:142px">Adults</span>
  <span class="lbl" style="left:242px;top:142px">Children (0-17)</span>
  <div class="field" style="left:11px;top:152px;width:71px">mm/dd/yyyy<span class="cal"></span></div>
  <div class="field" style="left:87px;top:152px;width:71px">mm/dd/yyyy<span class="cal"></span></div>
  <div class="field" style="left:165px;top:152px;width:71px">1<span class="chev"></span></div>
  <div class="field" style="left:242px;top:152px;width:71px">1<span class="chev"></span></div>

  <div class="abs checks"><span><i></i>Add a hotel</span><span><i></i>Add a car</span></div>
  <div class="abs btn-search">Search</div>
</form>

<section class="abs deals">
  <h2 class="section-title">Today's Top Deals</h2>
  <article class="deal-card" style="left:80px">
    <div class="photo" role="img" aria-label="Longtail boat on a tropical beach below a limestone cliff" style="background:linear-gradient(180deg,#2f77c6,#7fb4e0 55%,#d9c59a 80%,#b08a5a)"></div>
    <h3>Extra Savings on Your Escape</h3>
    <p>Lorem ipsum dolor sit amet, consectetur adipiscing elit, sed do eiusmod tempor incididunt ut labore et dolore magna aliqua.</p>
  </article>
  <article class="deal-card" style="left:273px">
    <div class="photo" role="img" aria-label="Wooden pier stretching into turquoise sea under a blue sky" style="background:linear-gradient(180deg,#1d5fc2,#5ca8e8 45%,#bfe6f2 62%,#22c7cf 80%,#17a9b8)"></div>
    <h3>Extra Savings on Your Escape</h3>
    <p>Lorem ipsum dolor sit amet, consectetur adipiscing elit, sed do eiusmod tempor incididunt ut labore et dolore magna aliqua.</p>
  </article>
  <article class="deal-card faded" style="left:465px">
    <div class="photo" role="img" aria-label="Paraglider silhouetted against a sunset sky over the sea" style="background:linear-gradient(180deg,#2b9fb0,#8cc4b6 55%,#e9c27a 85%,#d9a55a)"></div>
    <h3>Extra Savings on Your Escape</h3>
    <p>Lorem ipsum dolor sit amet, consectetur adipiscing elit, sed do eiusmod tempor incididunt ut labore et dolore magna aliqua.</p>
  </article>
  <div class="abs dots"><i></i><i class="on"></i><i></i></div>
</section>

<div class="promo" style="left:80px" role="img" aria-label="Green mountain valley under clouds with hand lettering reading The World For You" >
  <div style="position:absolute;inset:0;background:linear-gradient(180deg,#6f8796,#a9b9c0 35%,#4f8a5a 65%,#6da33a)"></div>
  <span class="btn-explore" style="left:22px">Explore More</span>
</div>
<div class="promo" style="left:273px" role="img" aria-label="Couple of hikers watching a golden sunset with hand lettering reading Treat Yourself">
  <div style="position:absolute;inset:0;background:linear-gradient(180deg,#e8b64a,#f0a33a 40%,#c0612a 75%,#7a3a1a)"></div>
  <span class="btn-explore" style="left:16px">Explore More</span>
</div>
<div class="promo" style="left:466px" role="img" aria-label="Hiker with a backpack on a mountain trail with hand lettering reading We Make Vacation">
  <div style="position:absolute;inset:0;background:linear-gradient(160deg,#5a5a4a,#7b8a80 40%,#5d7a7a 70%,#3f5a55)"></div>
  <span class="btn-explore" style="left:111px">Explore More</span>
</div>

<footer class="abs site-footer">
  <h2 style="left:80px">Find Cheap Tickets by Destination</h2>
  <h2 style="left:400px">Find Cheap Tickets by Airline</h2>
  <ul class="link-col" style="left:80px"><li>Flights to Fort Myers</li><li>Flights to Phoenix</li><li>Flights to Dallas</li><li>Flights to Ft. Lauderdale</li><li>Flights to San Diego</li><li>Flights to Chicago</li></ul>
  <ul class="link-col" style="left:196px"><li>Flights to Atlanta</li><li>Flights to San Francisco</li><li>Flights to Miami</li><li>Flights to Denver</li><li>Flights to San Juan</li><li>Flights to Orlando</li></ul>
  <ul class="link-col" style="left:298px"><li>Flights to Honolulu</li><li>Flights to Seattle</li><li>Flights to Las Vegas</li><li>Flights to Los Angeles</li><li>Flights to Orlando</li><li>Flights to Honolulu</li></ul>
  <ul class="link-col" style="left:400px"><li>Lumara Airlines</li><li>Brisk Airlines</li><li>Skyvora</li><li>Coralis Pacific Air</li><li>Starfield Airlines</li><li>Falconia Airlines</li></ul>
  <ul class="link-col" style="left:502px"><li>Fjordwing Air</li><li>Pearlgate Airways</li><li>Ridgeway Airlines</li><li>Unison Airlines</li><li>Air Sundara</li><li>Volanta</li></ul>
  <ul class="link-col" style="left:594px"><li>Dunevia</li><li>Glacierline Airlines</li><li>Air Maplestar</li><li>Tradewind Airlines</li><li>Bosphora Airlines</li><li>Jadewing Airlines</li></ul>
  <h3>Find Travel Deals by Destination</h3>
  <p class="about">To make your search for affordable travel easier, browse our selection of cheap airline tickets, hotel rates, car rentals and vacation packages in destinations across Africa, Asia, Caribbean, Central America, Europe, North America and South America.</p>
  <div class="rule"></div>
  <div class="copy">©2017 Rovanix.All right Reserved.</div>
  <span class="social" style="left:603px" aria-label="Social link"></span>
  <span class="social" style="left:620px" aria-label="Social link"></span>
  <span class="social" style="left:638px" aria-label="Social link"></span>
</footer>

</body>
</html>
```